Smart Routing SaaS needs a magic web design

We need a web design that focuses in the UX and conveys the idea of doing magic through our software. The company name is Brantiq and it is a word game about wow and slip... we are a software as a service B2B that helps companies automate dispatches and routes for their delivery guys to deliver goods to the customers. Think of it as an zephyr software applicable to your own fleet or third party fleets that can be used for example in a supermarket. That way the final user (buyer of the supermarket) knows where the parcel is, if it is leaving the store, if it is on its way, how long will it take to arrive, who is the delivery guy, etc... Brantiq's symbol is an owl. Think of it as the movie The Lanternkeep: Autumn's Oath, Queen Odalie had an owl mask and the ice owl who was her eyes on the field... that is the idea I want to convey through this software. It is the eyes for the business and the eyes for the final user. The software is comprised of a web platform (for the business with the fleet to manage) and the driver's application. The final customer receives the real time tracking information through SMS and email. The design should communicate magic through the use of the software... You can see some info on the existing webpage... which is very cold and dull... no life in it brantiq.example.. Use of gifs is desirable.

Text that can be used on the cover to convey main idea:

High end technology
We take care of your delivery management

The software that brings visibility and smartness to your deliveries through automated dispatches and smart routings
Our expertise: A Delightful Customer Experience of Deliveries

Target Market(s)

Professionals and businesses of all types with a delivery of any kind (supermarkets, pharmacies, restaurants, moving services, fleets, home services, deliveries, supply chain, field sales...)
Please look at competition webpages:
www.pathkit7.example
www.movra.example
www.trekly.example
vantacor.example
quickbarn.example
zephyr dash

Industry/Entity Type

Business Software

Coding

Coded - Design and coding required

Number of Pages Required

5+ page

Font styles to use
Other font styles liked:
• Modulus and Trade Gothic Ltd

Requirements
Must have
• MUST HAVE A D3JS LIKE:
• http://grafnode.example/jterran/5518302
• http://jterran.codepages.example/d3/talk/20111116/force-collapsible.html
• https://plinthware.example/hugo/fisheye/
• http://movingcharts.example/lab/d3-tree/
• A great magic capturing Homepage that conveys the main idea of what we are. A software that will help you manage your people on field who are getting something to the end customer (who will be aware of the live parcel status through SMS/ email notifications), we live in the cloud... no need of implementation fees, there is a free demo. Right now the webpage has an animation. Maybe a picture with a video on it could be something nice, or something that moves... take a look at zephyr dash. The main idea of the page should send the idea of something magic... use the owl... something that flies.
• The page must have gifs here and there... never stop the idea of a swift magic going on... efficiency on the logistics management of the company... happy customers.
• Parallax... I love parallax.
Nice to have
• The webpage may be telling a story... first what are we and what we do... how it works, who is our market, the benefits, hard facts on efficiency... please take a look at the current webpage www.brantiq.example to get more info but make it beautiful.
• A phrase here and there of why they need our service
Should not have
• I want to change the current idea of the webpage that the software aims only to manage fleets for home delivery... we are NOT a home delivery only management system. We can make any company's logistics "fly".
• I dont want to see dullness in the webpage, I am looking for a soul.

```html
<!DOCTYPE html>
<html lang="es">
<head>
<meta charset="utf-8">
<title>Brantiq — Software de alta tecnología</title>
<link href="https://fonts.googleapis.com/css2?family=Roboto:wght@300;400;500;700&family=Roboto+Condensed:wght@400;700&display=swap" rel="stylesheet">
<style>
  :root{
    --teal:#14b4d8;
    --teal-dark:#0e9cc0;
    --navy:#1d3550;
    --navy-deep:#162a40;
    --navy-light:#2c5378;
    --ink:#2a3440;
    --white:#ffffff;
    --muted:#9fb3c6;
    --footer-bg:#f1f2f3;
    --footer-ink:#7b8590;
  }
  *{box-sizing:border-box;margin:0;padding:0}
  html,body{width:1200px;height:3492px;overflow:hidden;background:var(--white)}
  body{font-family:"Roboto",Arial,sans-serif;color:var(--white)}
  .page{position:relative;width:1200px;height:3492px;overflow:hidden}
  .abs{position:absolute}
  .center{left:0;width:1200px;text-align:center}

  /* header */
  .site-header{position:absolute;top:0;left:0;width:1200px;height:72px;background:var(--white);z-index:5}
  .brand{position:absolute;left:228px;top:22px;font-size:24px;font-weight:500;color:var(--ink);letter-spacing:1px}
  .main-nav{position:absolute;right:210px;top:29px;display:flex;gap:58px;font-size:11px;letter-spacing:1px;color:#6b7580;font-weight:500}

  /* hero */
  .hero-photo{position:absolute;top:72px;left:0;width:1200px;height:900px;
    background:linear-gradient(180deg,#5d6a73 0%,#8a8676 35%,#a79a7f 55%,#6f7a80 80%,#4d5e6c 100%)}
  .hero-shade{position:absolute;top:72px;left:0;width:1200px;height:900px;background:rgba(20,30,45,.35)}
  .hero-title{top:178px;font-size:32px;font-weight:700;letter-spacing:1.5px}
  .hero-sub{top:226px;font-size:17px;font-weight:400;letter-spacing:1.5px}
  .play{left:568px;top:290px;width:64px;height:64px}
  .btn-trial{left:524px;top:386px;width:152px;height:36px;background:var(--teal);font-size:10px;font-weight:700;letter-spacing:1px;line-height:36px;text-align:center;color:var(--white)}
  .experts-title{top:490px;font-size:34px;font-weight:700;letter-spacing:1px}
  .experts-sub{top:546px;font-size:17px;letter-spacing:1.5px}
  .feature-label{font-size:12px;letter-spacing:1px;line-height:17px;color:var(--white)}
  .feature-label b{font-weight:700;display:block}
  .feature-label span{color:#d7dee4}

  .phone{left:484px;top:604px;width:240px;height:548px;border-radius:36px;background:#f5f6f7;border:2px solid #d9dde1;z-index:3}
  .phone-screen{position:absolute;left:14px;top:80px;width:208px;height:370px;background:linear-gradient(160deg,#dfe9e2,#cfdde6);border-radius:2px}
  .phone-speaker{position:absolute;left:92px;top:40px;width:52px;height:6px;border-radius:3px;background:#c9ced3}
  .phone-button{position:absolute;left:96px;top:470px;width:44px;height:44px;border-radius:50%;border:2px solid #d2d6da}

  /* how it works */
  .how-title{top:1228px;font-size:38px;font-weight:700;letter-spacing:1px}
  .step{position:absolute;top:1330px;width:200px;text-align:center}
  .step p{margin-top:20px;font-size:12px;line-height:20px;color:#d3dce5}
  .step p em{font-style:normal;color:var(--teal)}

  /* businesses */
  .biz-kicker{top:1880px;font-size:17px;letter-spacing:1.5px;font-weight:400}
  .biz-title{top:1908px;font-size:36px;font-weight:700;letter-spacing:.5px}
  .biz{position:absolute;width:200px;text-align:center}
  .biz-icon{width:136px;height:136px;margin:0 auto;border-radius:50%;background:var(--white);display:flex;align-items:center;justify-content:center;box-shadow:0 3px 0 rgba(0,0,0,.08)}
  .biz-label{margin-top:22px;font-size:12px;line-height:17px;letter-spacing:.5px;color:var(--navy-deep);font-weight:500}

  /* contact */
  .contact-photo{position:absolute;top:2596px;left:0;width:1200px;height:816px;
    background:linear-gradient(180deg,#3d4650 0%,#2c343d 50%,#1e252c 100%)}
  .contact-shade{position:absolute;top:2596px;left:0;width:1200px;height:816px;background:rgba(15,22,30,.45)}
  .grow-title{top:2646px;font-size:36px;font-weight:700;letter-spacing:.5px}
  .grow-sub{top:2706px;font-size:19px;letter-spacing:1px}
  .grow-tags{top:2776px;left:280px;width:640px;display:flex;justify-content:space-between;font-size:18px;font-weight:500;letter-spacing:1px;color:var(--teal)}
  .contact-form{position:absolute;left:228px;top:2880px;width:340px}
  .field{display:block;width:340px;height:44px;border-bottom:1px solid rgba(255,255,255,.35);font-size:11px;color:#b8c2cb;padding-top:18px;margin-bottom:6px}
  .field.message{height:70px}
  .btn-submit{display:block;margin-top:28px;width:92px;height:34px;background:var(--teal);text-align:center;line-height:34px;font-size:10px;font-weight:700;letter-spacing:1px}
  .agent{left:700px;top:2896px;width:224px;height:224px;border-radius:50%;background:radial-gradient(circle at 50% 40%,#e9eef2,#c2ccd4);border:4px solid var(--white)}
  .contact-info{left:640px;top:3138px;width:370px;text-align:center;font-size:11px;line-height:18px;color:#d5dde4}
  .contact-line{left:640px;top:3190px;width:370px;display:flex;justify-content:center;gap:24px;font-size:11px;color:#d5dde4}
  .socials{left:740px;top:3222px;display:flex;gap:10px}
  .socials i{display:block;width:22px;height:22px;border-radius:50%;background:#dfe5ea}
  .brand-foot{position:absolute;left:228px;top:3312px;font-size:26px;font-weight:500;letter-spacing:1px;color:var(--white)}

  .site-footer{position:absolute;top:3412px;left:0;width:1200px;height:80px;background:var(--footer-bg);font-size:11px;color:var(--footer-ink)}
  .site-footer .legal{position:absolute;left:228px;top:34px;display:flex;gap:40px}
  .site-footer .lang{position:absolute;right:220px;top:34px}
</style>
</head>
<body>
<div class="page">

  <header class="site-header">
    <div class="brand">Brantiq</div>
    <nav class="main-nav"><span>FUNCIONAMIENTO</span><span>NOSOTROS</span><span>CONTACTO</span><span>LOGIN</span></nav>
  </header>

  <!-- hero -->
  <div class="hero-photo" role="img" aria-label="Vista aérea de una ciudad con río y rascacielos"></div>
  <div class="hero-shade"></div>
  <h1 class="abs center hero-title">SOFTWARE DE ALTA TECNOLOGÍA</h1>
  <p class="abs center hero-sub">ENCARGADO DE TUS ENTREGAS A DOMICILIO</p>
  <svg class="abs play" viewBox="0 0 64 64"><circle cx="32" cy="32" r="29" fill="none" stroke="#fff" stroke-width="3"/><path d="M26 20 L45 32 L26 44Z" fill="#fff"/></svg>
  <div class="abs btn-trial">PRUEBALO GRATIS</div>
  <h2 class="abs center experts-title">SOMOS EXPERTOS EN</h2>
  <p class="abs center experts-sub">ADMINISTRACIÓN LOGÍSTICA Y ENTREGA A DOMICILIO CON:</p>
  <div class="abs feature-label" style="left:350px;top:650px"><b>RUTEO</b><span>INTELIGENTE</span></div>
  <div class="abs feature-label" style="left:800px;top:660px"><b>DESPACHOS</b><span>AUTOMATIZADOS</span></div>

  <!-- diagonal bands -->
  <svg class="abs" style="left:0;top:760px" width="1200" height="1900" viewBox="0 0 1200 1900">
    <polygon points="0,90 560,10 1200,120 1200,300 0,300" fill="var(--navy-light)" opacity=".85"/>
    <polygon points="0,130 1200,60 1200,1060 0,1060" fill="var(--navy)"/>
    <polygon points="0,220 1200,120 1200,1060 0,1060" fill="var(--navy-deep)" opacity=".35"/>
    <polygon points="0,960 1200,1040 1200,1840 0,1840" fill="var(--teal)"/>
  </svg>

  <div class="abs phone">
    <div class="phone-speaker"></div>
    <div class="phone-screen" role="img" aria-label="Pantalla de la app con mapa de ruta y marcadores de entrega"></div>
    <div class="phone-button"></div>
  </div>

  <!-- how it works -->
  <h2 class="abs center how-title">HOW IT WORKS?</h2>
  <div class="step" style="left:128px">
    <svg width="110" height="140" viewBox="0 0 110 140"><path d="M55 4 A50 50 0 0 1 92 88 L55 136 L18 88 A50 50 0 0 1 55 4Z" fill="#eef1f4"/><circle cx="55" cy="54" r="30" fill="#c7d2dc" role="img" aria-label="Ilustración de carga de órdenes"/></svg>
    <p><em>Ingresa tus órdenes</em> manualmente o desde un archivo CSV</p>
  </div>
  <div class="step" style="left:372px">
    <svg width="110" height="140" viewBox="0 0 110 140"><path d="M55 4 A50 50 0 0 1 92 88 L55 136 L18 88 A50 50 0 0 1 55 4Z" fill="#eef1f4"/><circle cx="55" cy="54" r="30" fill="#c7d2dc" role="img" aria-label="Ilustración de asignación de rutas"/></svg>
    <p>El sistema se encarga <em>de asignar el mensajero</em> y generar la <em>ruta óptima</em></p>
  </div>
  <div class="step" style="left:604px">
    <svg width="110" height="140" viewBox="0 0 110 140"><path d="M55 4 A50 50 0 0 1 92 88 L55 136 L18 88 A50 50 0 0 1 55 4Z" fill="#eef1f4"/><circle cx="55" cy="54" r="30" fill="#c7d2dc" role="img" aria-label="Ilustración de despacho del pedido"/></svg>
    <p><em>Se despacha el pedido</em> a través de la aplicación del mensajero</p>
  </div>
  <div class="step" style="left:852px">
    <svg width="110" height="140" viewBox="0 0 110 140"><path d="M55 4 A50 50 0 0 1 92 88 L55 136 L18 88 A50 50 0 0 1 55 4Z" fill="#eef1f4"/><circle cx="55" cy="54" r="30" fill="#c7d2dc" role="img" aria-label="Ilustración de notificación al cliente"/></svg>
    <p>Notifica a tus clientes con <em>visibilidad de tiempo real</em> de su pedido</p>
  </div>

  <!-- businesses -->
  <p class="abs center biz-kicker">NEGOCIOS DE PEDIDOS</p>
  <h2 class="abs center biz-title">NEGOCIOS DE PEDIDOS</h2>

  <div class="biz" style="left:128px;top:2024px">
    <div class="biz-icon"><svg width="70" height="60" viewBox="0 0 70 60"><path d="M6 22h58l-7 32H13Z" fill="#e8a13a"/><path d="M20 22 L30 6 M50 22 L40 6" stroke="#8a5a1f" stroke-width="4" fill="none"/><path d="M20 30v18M35 30v18M50 30v18" stroke="#b5731f" stroke-width="3"/></svg></div>
    <div class="biz-label">ENTREGA DE<br>SUPERMERCADOS</div>
  </div>
  <div class="biz" style="left:372px;top:2024px">
    <div class="biz-icon"><svg width="80" height="60" viewBox="0 0 80 60"><circle cx="40" cy="30" r="24" fill="#e04b3a"/><circle cx="40" cy="30" r="15" fill="#fff"/><path d="M8 8v44M72 8v44" stroke="#7c8792" stroke-width="4"/></svg></div>
    <div class="biz-label">ENTREGA DE<br>RESTAURANTES</div>
  </div>
  <div class="biz" style="left:620px;top:2024px">
    <div class="biz-icon"><svg width="60" height="60" viewBox="0 0 60 60"><g transform="rotate(-45 30 30)"><rect x="8" y="20" width="44" height="20" rx="10" fill="#7bbd42"/><path d="M30 20h12a10 10 0 0 1 0 20H30Z" fill="#e04b3a"/></g></svg></div>
    <div class="biz-label">ENTREGA DE<br>FARMACIAS</div>
  </div>
  <div class="biz" style="left:864px;top:2024px">
    <div class="biz-icon"><svg width="76" height="56" viewBox="0 0 76 56"><rect x="2" y="8" width="44" height="32" fill="#e8a13a"/><path d="M46 18h16l12 12v10H46Z" fill="#7bbd42"/><circle cx="16" cy="44" r="7" fill="#3a4550"/><circle cx="60" cy="44" r="7" fill="#3a4550"/></svg></div>
    <div class="biz-label">MANEJO DE<br>FLOTILLAS</div>
  </div>

  <div class="biz" style="left:128px;top:2324px">
    <div class="biz-icon"><svg width="70" height="64" viewBox="0 0 70 64"><path d="M4 26 L35 4 L66 26Z" fill="#e04b3a"/><rect x="12" y="26" width="46" height="34" fill="#7bbd42"/><rect x="29" y="40" width="12" height="20" fill="#3a4550"/></svg></div>
    <div class="biz-label">SERVICIOS<br>DEL HOGAR</div>
  </div>
  <div class="biz" style="left:372px;top:2324px">
    <div class="biz-icon"><svg width="76" height="56" viewBox="0 0 76 56"><rect x="2" y="4" width="48" height="36" fill="#7bbd42"/><path d="M50 16h14l10 12v12H50Z" fill="#e8a13a"/><circle cx="16" cy="44" r="7" fill="#3a4550"/><circle cx="60" cy="44" r="7" fill="#3a4550"/></svg></div>
    <div class="biz-label">MUDANZAS</div>
  </div>
  <div class="biz" style="left:620px;top:2324px">
    <div class="biz-icon"><svg width="70" height="60" viewBox="0 0 70 60"><path d="M4 6h10l8 34h36l6-24H18" fill="none" stroke="#3a4550" stroke-width="4" stroke-linejoin="round"/><circle cx="26" cy="50" r="5" fill="#3a4550"/><circle cx="54" cy="50" r="5" fill="#3a4550"/></svg></div>
    <div class="biz-label">COMERCIO<br>ELECTRÓNICO</div>
  </div>
  <div class="biz" style="left:864px;top:2324px">
    <div class="biz-icon"><svg width="76" height="50" viewBox="0 0 76 50"><path d="M4 30 L14 14 H52 L66 28 H72 V38 H4Z" fill="#e8a13a"/><rect x="20" y="18" width="14" height="9" fill="#fff"/><rect x="38" y="18" width="12" height="9" fill="#fff"/><circle cx="18" cy="40" r="7" fill="#3a4550"/><circle cx="58" cy="40" r="7" fill="#3a4550"/></svg></div>
    <div class="biz-label">ZEPHYR X</div>
  </div>

  <!-- contact -->
  <div class="contact-photo" role="img" aria-label="Calle de ciudad nocturna en tonos oscuros"></div>
  <div class="contact-shade"></div>
  <h2 class="abs center grow-title">BUSCAMOS HACER CRECER TU NEGOCIO</h2>
  <p class="abs center grow-sub">DE FORMA EFICIENTE CON</p>
  <div class="abs grow-tags"><span>LA ADMINISTRACIÓN</span><span>EFICIENTE DE</span><span>TUS FLOTILLAS</span></div>

  <form class="contact-form">
    <span class="field">Nombre</span>
    <span class="field">Email</span>
    <span class="field">Teléfono</span>
    <span class="field message">Mensaje</span>
    <span class="btn-submit">SUBMIT</span>
  </form>

  <div class="abs agent" role="img" aria-label="Fotografía de agente de atención al cliente con diadema"></div>
  <p class="abs contact-info">120 Calle Norte, Suite 4,<br>Ciudad Centro, CP 10500</p>
  <div class="abs contact-line">
    <span>
      <svg width="10" height="10" viewBox="0 0 10 10" style="vertical-align:-1px"><path d="M2 1l2 2-1 1.5a6 6 0 0 0 2.5 2.5L7 6l2 2-1 1.5A8 8 0 0 1 .5 2Z" fill="#d5dde4"/></svg>
      +1 (521) 555 0186
    </span>
    <span>
      <svg width="12" height="9" viewBox="0 0 12 9" style="vertical-align:-1px"><rect x=".5" y=".5" width="11" height="8" fill="none" stroke="#d5dde4"/><path d="M.5 .5 6 5l5.5-4.5" fill="none" stroke="#d5dde4"/></svg>
      info@brantiq.example
    </span>
  </div>
  <div class="abs socials"><i></i><i></i><i></i><i></i><i></i></div>

  <div class="brand-foot">Brantiq</div>

  <footer class="site-footer">
    <div class="legal"><span>© 2016, Brantiq. All right reserved.</span><span>Terms &amp; Conditions</span><span>Privacy policy</span><span>Disclaimer</span></div>
    <div class="lang">ES</div>
  </footer>
</div>
</body>
</html>
```